Form Sculptors Business Card

Professional cosmetic surgery company, based in very exclusive area in London. High profiled clientele. Brand is very artistic, modern, state-of-the-art, safe. The best in the business. Celebrity clientele.

Form Sculptor’s of London is a brand serving a discriminating and exclusive clientele who value personal service that is both intimate and high end. Our clients choose Form Sculptors because of the relationships we share with all of our customers. The clients of Form Sculptors have an equal partnership between customers, and very experienced, highly qualified medical professionals. This together provides you with a professional service that keeps you looking good and feeling good. It is a relationship based on honesty, compassion, loyalty and respect.
Form Sculptor’s have provided services for internationally recognised celebrities, and other high profiled individuals.

The cards are used for networking at private, exclusive events with VIPs.

Target Market(s)

Professionals
Rich people

Industry/Entity Type

Professional Service

Contact Information for Business Card

Need double sided business card design for 4 people. Back of the business card needs to have contrast background to the front with butterfly watermark with services provided:
Hair Restoration surgery
Hair Loss treatments
Breast surgery
Rhinoplasty
Pulvix Liposuction
Fat Grafting
Lumaxin & Fillers

Front of the business card needs to be a nice satin black.
with following information:
Calvert Osterlund - name
Chief Executive - Job title

www.formsculptors-example.co.uk
calvert@formsculptors-example.co.uk
Phone: +44 (0)207 946 0321
Mobile: +44 (0)7700 900 147

The London Farrowmere Clinic
14 Farrowmere Lane | London | W1X 4QP
Off Quenby Street

All business cards have the same address, phone, website as Calvert's details.
Same details on the back of the business card as well.
The other cards have different name, job title, email, mobile number

Teodor Lunn - Name
Partner - Job Title
Former England International Cricketer - please include below job title

email: teodor@formsculptors-example.co.uk
mobile: +44(0)7700 900582

Dr Castello Vranesk - Name
Plastic Surgeon - Job Title
drvranesk@formsculptors-example.co.uk
No mobile number

Dr Ezra Tolquist FRCS (please put FRCS in small font) - Name
Hair Restoration Surgeon - Job Title
drtolquist@formsculptors-example.co.uk
No mobile number

Colors
cedeec
85abd2
0655a3

Requirements
Must have
• The logo needs to be in a metallic finish
• Text needs to be striking
• nice background
• butterfly watermark on the back

```html
<!DOCTYPE html>
<html lang="en">
<head>
<meta charset="utf-8">
<title>Form Sculptors Business Card</title>
<link href="https://fonts.googleapis.com/css2?family=Lato:wght@400;700&display=swap" rel="stylesheet">
<style>
  :root {
    --page: #ececec;
    --slate: #3d3c3e;
    --paper: #ffffff;
    --ink: #2f2f31;
    --red: #d9233d;
    --red-dark: #9e1a2c;
    --orange: #f0812a;
    --green: #95c347;
    --blue: #1b99d6;
    --blue-dark: #12668f;
    --brand: #85abd2;
    --brand-deep: #0655a3;
    --mark: #cfcfcf;
  }
  * { margin: 0; padding: 0; box-sizing: border-box; }
  html, body {
    width: 1000px; height: 1200px; overflow: hidden;
    background: var(--page);
    font-family: "Lato", Arial, sans-serif;
  }
  .card {
    position: absolute; left: 60px;
    width: 880px; height: 524px;
    background: var(--paper);
    overflow: hidden;
    box-shadow: 0 2px 10px rgba(0,0,0,.12);
  }
  .card--front { top: 50px; }
  .card--back { top: 626px; }

  /* front */
  .front__panel {
    position: absolute; left: 0; top: 0;
    width: 471px; height: 100%;
    background: var(--slate);
  }
  .wordmark {
    position: absolute;
    font-weight: 700; letter-spacing: 1px;
    white-space: nowrap;
  }
  .front__wordmark {
    left: 80px; top: 258px;
    font-size: 36px; color: var(--brand);
  }
  .tab-column { position: absolute; }
  .front__tabs { left: 445px; top: 57px; }
  .details {
    position: absolute; left: 563px; top: 85px;
    color: var(--ink);
  }
  .details__name { font-size: 22px; font-weight: 400; text-transform: uppercase; line-height: 1.1; }
  .details__name strong { font-weight: 700; }
  .details__title { font-size: 19px; line-height: 1.2; }
  .details__group {
    position: absolute; left: 0; width: 320px;
    font-size: 19px; line-height: 1.45;
  }
  .details__address { top: 94px; }
  .details__phones { top: 186px; }
  .details__web { top: 280px; font-size: 17px; }

  /* back */
  .back__strip {
    position: absolute; top: 0; width: 53px; height: 100%;
    background: var(--slate);
  }
  .back__strip--left { left: 0; }
  .back__strip--right { right: 0; }
  .back__tabs--left { left: 57px; top: 57px; }
  .back__tabs--right { left: 755px; top: 57px; }
  .watermark {
    position: absolute; left: 160px; top: 36px;
    width: 380px; height: 462px;
    border-radius: 48% 48% 40% 40%;
    background: radial-gradient(ellipse at center, #d6d6d6 0%, #e4e4e4 55%, rgba(255,255,255,0) 75%);
  }
  .back__wordmark {
    left: 420px; top: 380px;
    font-size: 34px; color: var(--brand-deep);
  }
</style>
</head>
<body>

<section class="card card--front" aria-label="Business card front">
  <div class="front__panel">
    <p class="wordmark front__wordmark">Form Sculptors</p>
  </div>

  <svg class="tab-column front__tabs" width="93" height="400" viewBox="0 0 93 400" aria-hidden="true">
    <polygon points="0,14 93,14 93,0 0,14" fill="var(--red-dark)"/>
    <rect x="0" y="14" width="93" height="93" fill="var(--red)"/>
    <rect x="0" y="107" width="93" height="93" fill="var(--orange)"/>
    <rect x="0" y="200" width="93" height="93" fill="var(--green)"/>
    <rect x="0" y="293" width="93" height="93" fill="var(--blue)"/>
    <polygon points="0,386 93,386 0,400" fill="var(--blue-dark)"/>
    <!-- person -->
    <g fill="#fff">
      <circle cx="46.5" cy="50" r="10"/>
      <path d="M28 80 q0-18 18.5-18 q18.5 0 18.5 18 z"/>
    </g>
    <!-- house -->
    <g fill="#fff">
      <polygon points="46.5,136 24,156 30,156 46.5,141 63,156 69,156"/>
      <path d="M32 157 l14.5-12.5 l14.5 12.5 v15 h-10 v-10 h-9 v10 h-10 z"/>
    </g>
    <!-- phone -->
    <g fill="#fff">
      <path d="M28 236 q18.5-12 37 0 v6 h-8 v-5 q-10.5-5-21 0 v5 h-8 z"/>
      <path d="M35 244 h23 l5 18 h-33 z"/>
    </g>
    <circle cx="46.5" cy="252" r="4" fill="var(--green)"/>
    <!-- globe -->
    <g fill="none" stroke="#fff" stroke-width="2.5">
      <circle cx="46.5" cy="339.5" r="15"/>
      <ellipse cx="46.5" cy="339.5" rx="6.5" ry="15"/>
      <line x1="31.5" y1="339.5" x2="61.5" y2="339.5"/>
      <line x1="34" y1="331" x2="59" y2="331"/>
      <line x1="34" y1="348" x2="59" y2="348"/>
    </g>
  </svg>

  <div class="details">
    <h1 class="details__name"><strong>Calvert</strong> Osterlund</h1>
    <p class="details__title">Chief Executive</p>
    <p class="details__group details__address">The London Farrowmere<br>Clinic 14 Farrowmere Lane</p>
    <p class="details__group details__phones">+44 (0)207 946 0321<br>+44 (0)7700 900 147</p>
    <p class="details__group details__web">calvert@formsculptors-example.co.uk<br>www.formsculptors-example.co.uk</p>
  </div>
</section>

<section class="card card--back" aria-label="Business card back">
  <div class="back__strip back__strip--left"></div>
  <div class="back__strip back__strip--right"></div>

  <svg class="tab-column back__tabs--left" width="62" height="400" viewBox="0 0 62 400" aria-hidden="true">
    <polygon points="0,14 62,14 0,0" fill="var(--red-dark)"/>
    <rect x="0" y="14" width="62" height="93" fill="var(--red)"/>
    <rect x="0" y="107" width="62" height="93" fill="var(--orange)"/>
    <rect x="0" y="200" width="62" height="93" fill="var(--green)"/>
    <rect x="0" y="293" width="62" height="93" fill="var(--blue)"/>
    <polygon points="0,386 62,386 0,400" fill="var(--blue-dark)"/>
  </svg>
  <svg class="tab-column back__tabs--right" width="62" height="400" viewBox="0 0 62 400" aria-hidden="true">
    <polygon points="0,14 62,14 62,0" fill="var(--red-dark)"/>
    <rect x="0" y="14" width="62" height="93" fill="var(--red)"/>
    <rect x="0" y="107" width="62" height="93" fill="var(--orange)"/>
    <rect x="0" y="200" width="62" height="93" fill="var(--green)"/>
    <rect x="0" y="293" width="62" height="93" fill="var(--blue)"/>
    <polygon points="0,386 62,386 62,400" fill="var(--blue-dark)"/>
  </svg>

  <div class="watermark" role="img" aria-label="Faint butterfly watermark area"></div>
  <p class="wordmark back__wordmark">Form Sculptors</p>
</section>

</body>
</html>
```